Business Card - Tidal Lanes

Need Business Card design for company named Tidal Lanes. Software development focused mainly on Brindle Orvix & Zelt Apps. I've attached our logo with both a black and white background. Please add trademark symbol to logo when using.

```html
<!DOCTYPE html>
<html lang="en">
<head>
<meta charset="utf-8">
<title>Tidal Lanes — Business Card</title>
<link rel="stylesheet" href="https://fonts.googleapis.com/css2?family=Open+Sans:wght@400;600;700&display=swap">
<style>
  :root {
    --stage: #e6e7ea;
    --card-black: #0b0b0b;
    --amber: #f7a236;
    --gold: #fbc21b;
    --signal-red: #e0231c;
    --white: #ffffff;
    --ink: #1c1c1c;
  }
  * { box-sizing: border-box; margin: 0; padding: 0; }
  html, body {
    width: 1200px; height: 987px; overflow: hidden;
    background: var(--stage);
    font-family: "Open Sans", Arial, sans-serif;
  }
  .sheet {
    width: 1200px; height: 987px;
    display: flex; flex-direction: column; align-items: center; justify-content: center;
    gap: 44px;
  }
  .card {
    position: relative; width: 760px; height: 434px;
    border-radius: 30px; overflow: hidden;
    box-shadow: 0 10px 26px rgba(0,0,0,.18);
  }
  /* Front */
  .card--front { background: var(--card-black); }
  .card__wave { position: absolute; inset: 0; width: 100%; height: 100%; }
  .brand {
    position: absolute; left: 56px; top: 124px;
    display: flex; align-items: center; gap: 14px;
  }
  .brand__dot { width: 30px; height: 30px; border-radius: 50%; background: var(--amber); }
  .brand__name {
    color: var(--white); font-weight: 700; font-size: 42px; letter-spacing: -1px; white-space: nowrap;
  }
  .divider {
    position: absolute; left: 408px; top: 150px; width: 2px; height: 120px;
    background: linear-gradient(to bottom, rgba(255,255,255,0), rgba(255,255,255,.85), rgba(255,255,255,0));
    transform: rotate(18deg);
  }
  .contact { position: absolute; left: 440px; top: 130px; color: var(--white); }
  .contact__name { color: var(--amber); font-weight: 700; font-size: 34px; line-height: 1.1; }
  .contact__title { font-size: 22px; margin-bottom: 18px; }
  .contact__line { display: flex; align-items: center; gap: 12px; font-size: 25px; margin-top: 6px; }
  .contact__icon { width: 22px; height: 22px; flex: none; }
  .address {
    position: absolute; left: 30px; top: 394px;
    font-size: 16px; color: var(--ink); white-space: nowrap;
  }
  /* Back */
  .card--back {
    background: linear-gradient(110deg, var(--gold) 0%, var(--amber) 100%);
    display: flex; flex-direction: column; align-items: center; justify-content: center;
  }
  .card--back .brand { position: static; }
  .card--back .brand__dot { width: 34px; height: 34px; background: var(--white); }
  .card--back .brand__name { font-size: 62px; }
  .website {
    margin-top: 56px; color: var(--white); font-size: 20px; letter-spacing: 2px;
  }
</style>
</head>
<body>
<main class="sheet">
  <section class="card card--front" aria-label="Card front">
    <svg class="card__wave" viewBox="0 0 760 434" preserveAspectRatio="none" aria-hidden="true">
      <defs>
        <linearGradient id="bandFill" x1="0" y1="0" x2="1" y2="1">
          <stop offset="0" stop-color="#f7a236"/>
          <stop offset="1" stop-color="#fbc21b"/>
        </linearGradient>
      </defs>
      <path d="M0 244 C 150 250, 230 330, 380 380 S 640 410, 760 386 L760 434 L0 434 Z" fill="var(--signal-red)"/>
      <path d="M0 256 C 150 262, 225 342, 375 392 S 640 420, 760 398 L760 434 L0 434 Z" fill="url(#bandFill)"/>
    </svg>
    <div class="brand">
      <span class="brand__dot"></span>
      <span class="brand__name">Tidal Lanes™</span>
    </div>
    <div class="divider"></div>
    <div class="contact">
      <p class="contact__name">Your Name</p>
      <p class="contact__title">Title</p>
      <p class="contact__line">
        <svg class="contact__icon" viewBox="0 0 24 24" aria-hidden="true"><rect x="6" y="2" width="12" height="20" rx="2" fill="var(--amber)"/><rect x="8" y="5" width="8" height="9" fill="var(--card-black)"/><circle cx="12" cy="18" r="1.5" fill="var(--card-black)"/></svg>
        555-201-4410
      </p>
      <p class="contact__line">
        <svg class="contact__icon" viewBox="0 0 24 24" aria-hidden="true"><path d="M3 9 C3 5 21 5 21 9 L18 10 L16 8 L8 8 L6 10 Z" fill="var(--amber)"/><rect x="5" y="12" width="14" height="9" rx="2" fill="var(--amber)"/><circle cx="12" cy="16.5" r="2" fill="var(--card-black)"/></svg>
        555-201-7782
      </p>
    </div>
    <p class="address">4210 Harbor Row N, Calder, FL 30412</p>
  </section>

  <section class="card card--back" aria-label="Card back">
    <div class="brand">
      <span class="brand__dot"></span>
      <span class="brand__name">Tidal Lanes™</span>
    </div>
    <p class="website">www.tidallanes.com</p>
  </section>
</main>
</body>
</html>
```